Packaging for Biscuit Pups (filled with chocolate!)

Who wouldn't want to eat a small cookie filed with creamy chocolate or vanilla?

This product is a cookie outside with a chocolate filling.

They are bite sized.

It will be a wrapper, 10cm by about 15cm (photo of one attached)

The product is called "Zippa Pup".

"Zippa Pup" does not have a logo. It just needs some sort of bubbly font that looks playful.

The elements I would like to retain:
Some form of a bear. I prefer one that looks much cuter!
The images of the actual cookie. (the bears with the drawings on them)
"Chocolate" or "Vanilla"

I look forward to your designs!

Some designs from other companies from other countries are attached.
Updates

I added a photo of my older pack.  I am looking for the "next generation" of this package.

It does not need to be completely different that this. I would like to just spruce up my old design.

OR, if you have a very cool idea, I'd love to see that as well!

Target Market(s)

Kids 5-20

Industry/Entity Type

Product

Requirements
Must have
• Attached are photos of the products, and the images of my current packaging.

The package will be a wrapper, as attached in another photo.

```html
<!DOCTYPE html>
<html lang="en">
<head>
<meta charset="utf-8">
<title>Zippa Pup — Vanilla Wrapper</title>
<link rel="stylesheet" href="https://fonts.googleapis.com/css2?family=Fredoka:wght@600;700&display=swap">
<style>
  :root {
    --page: #ffffff;
    --wrapper-cream: #f4edc6;
    --wrapper-light: #faf6dc;
    --crimp-line: #e3d9a6;
    --label-fill: #f8f0c2;
    --brown: #5b3a21;
    --brown-mid: #8a5a34;
    --brown-soft: #b07a4c;
  }
  * { box-sizing: border-box; margin: 0; padding: 0; }
  html, body {
    width: 1200px;
    height: 900px;
    overflow: hidden;
    background: var(--page);
    font-family: "Fredoka", "Arial Rounded MT Bold", sans-serif;
  }
  .canvas {
    position: relative;
    width: 1200px;
    height: 900px;
  }

  /* Wrapper, sized by --u */
  .wrapper {
    position: absolute;
    width: calc(var(--u) * 56);
    height: calc(var(--u) * 80);
    background: linear-gradient(100deg, var(--wrapper-cream) 0%, var(--wrapper-light) 45%, var(--wrapper-cream) 100%);
    border-radius: calc(var(--u) * 1);
    box-shadow: 0 calc(var(--u) * 0.6) calc(var(--u) * 2.4) rgba(60, 40, 20, 0.18);
    overflow: hidden;
  }
  .wrapper--large { --u: 10px; left: 110px; top: 50px; }
  .wrapper--small { --u: 4px; left: 830px; top: 330px; }

  .crimp {
    position: absolute;
    left: 0;
    width: 100%;
    height: calc(var(--u) * 3.6);
    background: repeating-linear-gradient(90deg, var(--crimp-line) 0 calc(var(--u) * 0.25), transparent calc(var(--u) * 0.25) calc(var(--u) * 1));
    opacity: 0.8;
  }
  .crimp--top { top: 0; }
  .crimp--bottom { bottom: 0; }

  .mascot {
    position: absolute;
    left: calc(var(--u) * 13);
    top: calc(var(--u) * 5);
    width: calc(var(--u) * 30);
    height: calc(var(--u) * 24);
    border-radius: 48% 48% 40% 40%;
    background: radial-gradient(circle at 50% 45%, var(--brown-soft) 0%, var(--brown-mid) 70%, var(--brown) 100%);
  }

  .label {
    position: absolute;
    left: calc(var(--u) * 3);
    top: calc(var(--u) * 24);
    width: calc(var(--u) * 50);
    height: calc(var(--u) * 29);
    border-radius: 50%;
    background: var(--label-fill);
    border: calc(var(--u) * 0.7) solid var(--brown);
    display: flex;
    flex-direction: column;
    align-items: center;
    justify-content: center;
  }
  .brand-name {
    color: var(--brown);
    font-weight: 700;
    font-size: calc(var(--u) * 10.5);
    line-height: 0.95;
    text-align: center;
    letter-spacing: calc(var(--u) * 0.1);
  }

  .flavour {
    position: absolute;
    left: 0;
    width: 100%;
    top: calc(var(--u) * 53.5);
    text-align: center;
    color: var(--brown);
    font-weight: 700;
    font-size: calc(var(--u) * 8.5);
    line-height: 1.15;
    letter-spacing: calc(var(--u) * 0.4);
  }

  .cookie-mark {
    position: absolute;
    right: calc(var(--u) * 13);
    bottom: calc(var(--u) * 5);
    width: calc(var(--u) * 10);
    height: calc(var(--u) * 10);
    border-radius: 40%;
    background: radial-gradient(circle at 50% 40%, var(--brown-mid), var(--brown));
  }
  .cookie-caption {
    position: absolute;
    right: calc(var(--u) * 24.5);
    bottom: calc(var(--u) * 6);
    width: calc(var(--u) * 15);
    text-align: center;
    color: var(--brown);
    font-weight: 600;
    font-size: calc(var(--u) * 1.9);
    line-height: 1.1;
    transform: rotate(-18deg);
  }

  .corner-brand {
    position: absolute;
    right: 60px;
    top: 60px;
    color: var(--brown);
    font-weight: 700;
    font-size: 34px;
    line-height: 0.95;
    text-align: center;
  }
</style>
</head>
<body>
<main class="canvas">

  <section class="wrapper wrapper--large">
    <div class="crimp crimp--top"></div>
    <div class="mascot" role="img" aria-label="Illustration of a cute brown pup peeking over the label"></div>
    <div class="label">
      <p class="brand-name">Zippa<br>Pup</p>
    </div>
    <p class="flavour">vanilla</p>
    <p class="cookie-caption">vanilla<br>biscuit pups</p>
    <div class="cookie-mark" role="img" aria-label="Illustration of a pup-shaped biscuit"></div>
    <div class="crimp crimp--bottom"></div>
  </section>

  <section class="wrapper wrapper--small">
    <div class="crimp crimp--top"></div>
    <div class="mascot" role="img" aria-label="Illustration of a cute brown pup peeking over the label"></div>
    <div class="label">
      <p class="brand-name">Zippa<br>Pup</p>
    </div>
    <p class="flavour">vanilla</p>
    <p class="cookie-caption">vanilla<br>biscuit pups</p>
    <div class="cookie-mark" role="img" aria-label="Illustration of a pup-shaped biscuit"></div>
    <div class="crimp crimp--bottom"></div>
  </section>

  <p class="corner-brand">Zippa<br>Pup</p>

</main>
</body>
</html>
```